Wordpress Design Project - Leadership Guide Nest

Website Brief

We are looking to have a design produced for a modern professional website. A mind map of the site can be found here: http://www.thoughtlattice.example/view.htm?m=58142736a1b94c07d2e5f8a3c6b71d09

Each of the green tabs are pages just next to them is a very small green globe. If you click this. It will take you through to an example page for that section.

Task description
The website will be made up of:
1. A homepage (this will be the blog see http://www.janetquillby.example for an example of the crisp and cleanness we are looking for)
2. A page that will have just a video and option page (see: http://tvpgacademy.example/ for example)
3. 3 pages all with the same structure. (see: http://tvpgacademy.example/qw72plx19bnv/ for an example). Each will have:
a. A video
b. Tabs at the top of the video that link to the 3 videos and the sales page
c. Link to a resource download
d. Reader Comments section
4. 2 Page with about the experts and about our company (same style for both)
5. A page that will have a long well designed sales page (see: http://tvpgacademy.example/early-enrollment-2013/ for an example)
6. A page with testimonials on it (see http://www.janetquillby.example/praise/)
7. A page that will describe the products, services and provision we will be offering
8. A page that will detail our involvement with charities and not for profits

Must Have
Edgey, crisp design, similar to Janet Quillbys. We would like the colours to match very well throughout the site and have a unique font (possibly manksans). We want it to have very clean integrations between copy and images with shadows on videos for example like with Janetquillbys page. We really love this design and would like this to be the inspiration for our site however it would need to certainly have a more executive feel to suit our target market.

We like the idea of some kind of circles, crisp clean lines, nice white space, simple design, corporate looking, communicates wealth/success/massive value. Based on the two logos of NDLTR and the Hub (see attached)

Target Market:
The target market includes intelligent, productive coaches, who are self employed or part of small firms. They are well educated, well read, socially conscious, and committed to making a profound difference with their clients...skilled at the actions of coaching, but not the business side. There will be a ratio of approximately 60% male / 40% female (really? The coaching industry is predominantly female, no?), with an age range of 40 to 60 years. English is our core language. Most will have secondary education and the salary range will be $90,000 to $400,000. We will have a global audience reach, although the primary markets will be North America, Europe and Australia/NZ.

Marketing Objective:
LGN will be an on-line resource for Executive Coaches. The intent of the design will be to present LGN to the world as a highly professional organization. The intent is not to characterize LGN as solely corporate, but will also incorporate elements of entrepreneurialism. We require the brand to incorporate these values:
• Trustworthy – you can trust us
• Professional – we are true professionals whose mission is to provide value to our clients
• Caring - Interested in our clients wellbeing – we are keenly interested in helping our clients build their knowledge, skills, and attitudes to be highly productive and successful
• Successful
• Knowledgeable – we have breadth and depth of knowledge in leadership
• World-class – we have a world-wide target market and, as such, need the brand to reflect a powerful and inclusive image
• Positive Energy - I would like the brand to have positive energy and very clean feng shui
• Prestige
• Massive Value
• Accessible
• Worldly/ Sophisticated
• Affordable
• Mission-critical

Details about the needs, wants, aspirations etc. of our target market
Executive coaches need a process and a system for creating opportunities to do the work they love with clients who are qualified to engage them and pay them. There is a scarcity mentality around their own finances, but ironically an abundance mentality for what's possible in the world and for their clients. They want to make a difference, they want to facilitate transformation, they want to be of deep service.

They aspire to make a decent living doing it! They need help bridging the gap between practitioner/service provider and financially successful entrepreneur/business owner/ leader. They also aspire to have it be easy, as it feels hard for them to generate the revenues they want to generate solely through coaching, so many turn to training, speaking, and other revenue streams.

Required assets to send through to web designer
1. Three blog posts. Each will have:
a. A video/audio
b. Summary of the points raised
c. Download (possibly slides)
2. A page that will have just a video and option page
a. Headline
b. Video
c. One paragraph summary of what we do
3. 3 launch videos. Here for each we will need
a. A video scripted and produced
b. Title for each
c. A resource download
4. Sales page
a. Video
b. Copy
i. Overview
ii. Content of course
iii. Guarentee
iv. Details of bonuses
v. Details of support
vi. Pricing broken down ($30,000 value = $2000)
c. Animated Gif
5. About the company and experts
a. Description of our company, it's vision, mission, purpose and core values.
b. Description of each of us,
i. our key facts and wows,
ii. a picture of us
iii. some interesting facts (giving personality)
iv. Lower down we will add in "Faculty" these will be any thought leaders we invite in to be part of the value delivery (will add to our credibility having such a strong team behind the project)
6. Testimonials
a. Testimonials from coaches from working with us
7. Products, services and provision we will be offering
a. A simple description of each of the key products/services we will be offering
i. Leadership Guide Sales
ii. Leadership Guide Marketing
iii. Leadership Guide Help
iv. Leadership Guide Roundtable
v. Leadership Guide Resources
a. List of the various charity work each of us have been involved with

Requirements
Must have
• Edgey, crisp design, similar to Janet Quillbys. We would like the colours to match very well throughout the site and have a unique font (possibly manksans). We want it to have very clean integrations between copy and images with shadows on videos for example like with Janetquillbys page. We really love this design and would like this to be the inspiration for our site however it would need to certainly have a more executive feel to suit our target market.

```html
<!DOCTYPE html>
<html lang="en">
<head>
<meta charset="utf-8">
<title>Leadership Guide Nest</title>
<link rel="stylesheet" href="https://fonts.googleapis.com/css2?family=Quicksand:wght@400;500;700&family=Arimo:wght@400;700&display=swap">
<style>
:root{
  --orange:#e8b04c;
  --orange-dark:#cf9634;
  --orange-title:#e07b3c;
  --grey-band:#7d7d7d;
  --grey-bg:#dcdadb;
  --white:#ffffff;
  --page:#f4f4f4;
  --text:#6a6a6a;
  --text-dark:#4a4a4a;
  --line:#d6d6d6;
  --blue:#4f6ea8;
  --blue-soft:#9aadd0;
}
*{box-sizing:border-box;margin:0;padding:0}
html,body{width:866px;height:1200px;overflow:hidden}
body{font-family:"Arimo",Arial,sans-serif;color:var(--text);background:var(--page)}
h2,h3{font-weight:400}
.site{position:relative;width:866px;height:1200px;overflow:hidden}
.abs{position:absolute}

/* header */
.header{left:0;top:0;width:866px;height:96px;background:var(--page)}
.brand{left:168px;top:26px;display:flex;align-items:center;gap:8px}
.brand-dot{width:22px;height:22px;border-radius:50%;background:var(--orange)}
.brand-name{font-family:"Quicksand",sans-serif;font-weight:400;font-size:13px;color:var(--text)}
.util-links{right:176px;top:12px;font-size:7px;color:var(--orange-dark)}
.util-links span{margin:0 3px;color:#aaa}
.callus{right:176px;top:38px;font-family:"Quicksand",sans-serif;font-size:9.5px;color:var(--orange-dark);display:flex;align-items:center;gap:4px}
.search{left:537px;top:66px;width:153px;height:21px;border:1px solid var(--orange);border-radius:2px;background:#fff;font-size:7px;color:#b8a27a;padding:6px 10px}
.search svg{position:absolute;right:8px;top:5px}

/* nav */
.nav{left:0;top:96px;width:866px;height:36px;background:linear-gradient(#eebc5c,#e2a640);border-bottom:3px solid #f1c777}
.nav ul{list-style:none;display:flex;position:absolute;left:169px;top:11px}
.nav li{font-family:"Quicksand",sans-serif;font-size:10.5px;color:#fff;padding:0 18px;border-left:1px solid #d3973a}
.nav li:first-child{padding-left:0;border-left:0}

/* hero */
.hero{left:0;top:132px;width:866px;height:246px;background:linear-gradient(#9a9a9a,#6f6f6f 70%,#8b8b8b);border-bottom:4px solid var(--orange)}
.screen{left:163px;top:10px;width:528px;height:212px;background:#fff;border-radius:4px;box-shadow:0 3px 8px rgba(0,0,0,.35)}
.hero-photo{left:13px;top:12px;width:502px;height:188px;background:linear-gradient(90deg,#8fa6c4,#c9d3df 45%,#eef1f4 80%,#f7f8fa)}
.hero-title{left:352px;top:28px;width:155px;font-family:"Quicksand",sans-serif;font-weight:400;font-size:27px;line-height:28px;color:var(--orange-title);white-space:nowrap}
.hero-title small{display:block;font-size:17px;line-height:20px}
.hero-sub{left:355px;top:80px;width:155px;font-size:6.3px;line-height:8px;color:#666}
.stand{left:190px;top:212px;width:144px;height:18px;background:linear-gradient(#e6e6e6,#cfcfcf);border-radius:0 0 3px 3px}
.dots{left:0;top:5px;width:144px;display:flex;justify-content:center;gap:8px}
.dots i{width:7px;height:7px;border-radius:50%;background:#c4c4c4;border:1px solid #aaa}
.dots i:first-child{background:#888}

/* welcome */
.welcome{left:0;top:378px;width:866px;height:172px;background:var(--page)}
.h-section{font-family:"Quicksand",sans-serif;font-weight:400;font-size:17px;color:var(--orange-title)}
.para{font-size:6.3px;line-height:8.6px;color:var(--text);text-align:justify}
.btn{background:linear-gradient(#ecb655,#d99c36);color:#fff;font-size:7.5px;border-radius:3px;text-align:center}
.video{left:506px;top:47px;width:184px;height:106px;border:3px solid #cfcfcf;border-radius:3px;background:linear-gradient(120deg,#c7cfc6,#8d8f92 50%,#3f4246)}
.video-bar{left:0;bottom:0;width:100%;height:13px;background:rgba(30,30,30,.75)}
.play{left:72px;top:28px;width:34px;height:34px;background:rgba(232,176,76,.85);border-radius:3px}

/* content */
.content{left:0;top:550px;width:866px;height:596px;background:var(--grey-bg)}
.card{background:#fff;border-radius:3px;box-shadow:0 1px 3px rgba(0,0,0,.12)}
.post-title{font-family:"Quicksand",sans-serif;font-weight:400;font-size:10px;color:var(--orange-title)}
.date{width:23px;height:23px;background:var(--orange-dark);color:#fff;text-align:center;font-weight:700;font-size:9px;line-height:12px;border-radius:2px}
.date small{display:block;font-size:3.5px;line-height:5px;font-weight:400;background:#9b9b9b}
.tab-comments{background:var(--orange-dark);color:#fff;font-size:6.5px;padding:3px 10px 3px 12px}
.band{background:linear-gradient(#e4aa45,#d19a3a)}
.post-photo{border-radius:2px}
.post-text{font-size:5.4px;line-height:10.4px;color:#555}
.post-text p{margin-bottom:5px}
.share{display:flex;align-items:center;gap:4px;font-size:5.5px;color:#555;border-top:1px dotted #bbb;border-bottom:1px dotted #bbb;height:16px}
.share b{font-weight:400;border:1px solid #c9c9c9;border-radius:2px;padding:1px 3px;background:#f3f3f3}
.share em{font-style:normal;border:1px solid #ccc;padding:1px 3px}
.share .more{margin-left:auto}

/* form */
.form-head{left:24px;top:0;width:137px;height:28px;background:linear-gradient(#ecb655,#d99c36);color:#fff;font-family:"Quicksand",sans-serif;font-size:9.5px;text-align:center;line-height:28px}
.field{left:24px;width:137px;height:20px;border:1px solid #cfcfcf;box-shadow:inset 0 1px 2px rgba(0,0,0,.08);font-size:7px;color:#999;padding:5px 10px}

/* testimonials */
.h-testi{font-family:"Quicksand",sans-serif;font-weight:400;font-size:16px;color:var(--text-dark)}
.quote-photo{left:7px;top:9px;width:51px;height:51px;background:linear-gradient(#d8d3cc,#8f8a86)}
.fb-head{left:0;top:0;width:185px;height:25px;background:linear-gradient(#a3b2d2,#8b9dc4);color:#fff;font-family:"Quicksand",sans-serif;font-size:13px;padding:4px 12px;border-radius:3px 3px 0 0}
.avatar{width:28px;height:28px;background:linear-gradient(#c8b59a,#7a6a58)}
.fb-text{font-size:5.3px;line-height:8px;color:var(--blue)}
.fb-text small{display:block;color:#888;font-size:4.5px}

/* footer */
.footer{left:0;top:1146px;width:866px;height:54px;background:linear-gradient(#e2a640,#d4953a);border-top:3px solid #f0c470}
.foot-links{left:194px;top:18px;font-size:7px;color:#fff;line-height:11px}
.foot-links span{margin:0 3px}
.socials{left:579px;top:16px;display:flex;gap:4px}
.socials i{width:20px;height:20px;border-radius:50%;background:#fff;opacity:.95}
</style>
</head>
<body>
<div class="site">

  <header class="header abs">
    <div class="brand abs"><span class="brand-dot"></span><span class="brand-name">LeadershipGuideNest.com</span></div>
    <div class="util-links abs">Link<span>|</span>Support<span>|</span>Sitemap<span>|</span>Help</div>
    <div class="callus abs">
      <svg width="8" height="10" viewBox="0 0 8 10"><path d="M2 0 L4 2 L3 4 Q4 6 5 7 L7 6 L8 8 L6 10 Q0 7 0 2 Z" fill="#cf9634"/></svg>
      Call Us: 1-300-555 0142
    </div>
    <div class="search abs">Search
      <svg width="8" height="9" viewBox="0 0 8 9"><circle cx="3.3" cy="3.3" r="2.5" fill="none" stroke="#cf9634" stroke-width="1.2"/><line x1="5" y1="5" x2="7.5" y2="8" stroke="#cf9634" stroke-width="1.4"/></svg>
    </div>
  </header>

  <nav class="nav abs">
    <ul>
      <li>HOME</li><li>ABOUT US</li><li>WORK WITH US</li><li>TESTIMONIALS</li><li>GIVING BACK</li><li>CONTACT</li>
    </ul>
  </nav>

  <section class="hero abs">
    <div class="screen abs">
      <div class="hero-photo abs" role="img" aria-label="Photo of two businessmen in an office reviewing documents together"></div>
      <div class="hero-title abs">Leadership<small>GuideNest.com</small></div>
      <p class="hero-sub abs">At vero eos et accusamus et iusto odio dignissimos ducimus qui blanditiis praesentium</p>
      <div class="stand abs"><div class="dots abs"><i></i><i></i><i></i><i></i><i></i></div></div>
    </div>
  </section>

  <section class="welcome abs">
    <h2 class="h-section abs" style="left:162px;top:17px">Welcome to Our Site</h2>
    <div class="abs" style="left:162px;top:44px;width:320px">
      <p class="para" style="margin-bottom:8px">At vero eos et accusamus et iusto odio dignissimos ducimus qui blanditiis praesentium voluptatum deleniti atque corrupti quos dolores etquas molestias excepturi sint occaecati cupiditate non provident, similique sunt in culpa qui officia deserunt mollitia animi, illaborum et dolorum fuga. Et harum quidem rerum facilis est et expedita distinctio.</p>
      <p class="para">Nam libero tempore, cum soluta nobis est eligendi optio cumque nihil impedit quo minus id quod maxime placeat facere possil, omnis voluptas assumenda est, omnis dolor repellendus. At vero eos et accusamus et iusto odio dignissimos ducimus qui blanditiis praesentium voluptatum deleniti atque corrupti quos dolores etquas molestias excepturi sint occaecati cupiditate non provident.</p>
    </div>
    <div class="btn abs" style="left:162px;top:135px;width:61px;height:20px;line-height:20px">View More</div>

    <h2 class="h-section abs" style="left:505px;top:17px">Our Video</h2>
    <span class="abs" style="left:653px;top:26px;font-size:6.5px;color:var(--orange-dark)">View More..</span>
    <div class="video abs" role="img" aria-label="Video still of two businesswomen talking in a bright office">
      <div class="play abs"><svg width="34" height="34" viewBox="0 0 34 34"><path d="M12 9 L25 17 L12 25 Z" fill="#fff"/></svg></div>
      <div class="video-bar abs">
        <svg width="178" height="13" viewBox="0 0 178 13"><rect x="20" y="3" width="8" height="7" fill="#e8b04c"/><rect x="34" y="5.5" width="98" height="2" fill="#888"/><rect x="34" y="5.5" width="22" height="2" fill="#e8b04c"/><rect x="138" y="7" width="2" height="3" fill="#e8b04c"/><rect x="141" y="5" width="2" height="5" fill="#e8b04c"/><rect x="144" y="3" width="2" height="7" fill="#e8b04c"/></svg>
      </div>
    </div>
  </section>

  <main class="content abs">
    <article class="card abs" style="left:193px;top:15px;width:287px;height:566px">
      <h3 class="post-title abs" style="left:10px;top:9px">BURNT OUT VS. TIME FOR A CHANGE</h3>
      <div class="band abs" style="left:0;top:31px;width:287px;height:52px"></div>
      <div class="tab-comments abs" style="left:5px;top:25px">100 Comments</div>
      <div class="post-photo abs" style="left:11px;top:47px;width:262px;height:73px;background:linear-gradient(90deg,#e8e4df,#b9c2cc 50%,#dfe3e8)" role="img" aria-label="Photo of three smiling professionals at work"></div>
      <div class="post-text abs" style="left:11px;top:126px;width:262px">
        <p>Imagine this . . .<br>You love what you do and you're successful at it: making money, great clients, great team, etc. For years, you've worked your buns off to make this dream come to life.But here's the problem.</p>
        <p>Something's changed. You don't feel excited about what you do anymore.Most days, you feel kind of down and lost. And the truth is that you've been feeling this way for longer than you care to admit!So what do you do?And how can you tell the difference between normal burnout vs. a sign that it's time for a big change in your career?</p>
      </div>
      <div class="share abs" style="left:11px;top:223px;width:262px"><b>Like</b><em>164</em><b>Share</b><em>199</em><b>Plus</b><em>4</em><b>Save</b><em>11</em><span class="more">View More &gt;</span></div>

      <h3 class="post-title abs" style="left:10px;top:257px">BURNT OUT VS. TIME FOR A CHANGE</h3>
      <div class="band abs" style="left:0;top:279px;width:287px;height:52px"></div>
      <div class="tab-comments abs" style="left:5px;top:273px">100 Comments</div>
      <div class="post-photo abs" style="left:11px;top:295px;width:262px;height:73px;background:linear-gradient(90deg,#8a7566,#d8b9a0 40%,#c69b7e 70%,#6a8db8)" role="img" aria-label="Photo of happy young women talking on phones"></div>
      <div class="post-text abs" style="left:11px;top:374px;width:262px">
        <p>Imagine this . . .<br>You love what you do and you're successful at it: making money, great clients, great team, etc. For years, you've worked your buns off to make this dream come to life.But here's the problem.</p>
        <p>Something's changed. You don't feel excited about what you do anymore.Most days, you feel kind of down and lost. And the truth is that you've been feeling this way for longer than you care to admit!So what do you do?And how can you tell the difference between normal burnout vs. a sign that it's time for a big change in your career?</p>
        <p>great clients, great team, etc. For years, you've worked your buns off to make this dream come to life.But here's the problem.</p>
        <p>Something's changed. You don't feel excited about what you do anymore.Most days, you feel kind of down and lost. And the truth is that you've been feeling this way for longer than you care to admit!So what do you do?And how can you</p>
      </div>
      <div class="share abs" style="left:11px;top:537px;width:262px"><b>Like</b><em>164</em><b>Share</b><em>199</em><b>Plus</b><em>4</em><b>Save</b><em>11</em><span class="more">View More &gt;</span></div>
    </article>
    <div class="date abs" style="left:163px;top:40px">30<small>11:30am</small></div>
    <div class="date abs" style="left:163px;top:288px">30<small>11:30am</small></div>

    <section class="card abs" style="left:505px;top:15px;width:185px;height:204px">
      <div class="form-head abs">FILL OUR OPTION FORM</div>
      <div class="field abs" style="top:37px">Full Name</div>
      <div class="field abs" style="top:64px">Email ID</div>
      <div class="field abs" style="top:91px">Phone No.</div>
      <div class="field abs" style="top:118px;height:55px">Message</div>
      <div class="btn abs" style="left:25px;top:182px;width:50px;height:20px;line-height:20px;font-size:9px;font-family:'Quicksand',sans-serif;border-radius:0">Submit</div>
    </section>

    <h2 class="h-testi abs" style="left:505px;top:232px">Testimonials</h2>
    <div class="card abs" style="left:504px;top:263px;width:187px;height:67px">
      <div class="quote-photo abs" role="img" aria-label="Portrait of a smiling businessman"></div>
      <div class="abs" style="left:64px;top:9px;width:116px;font-size:7px;line-height:9px;color:#666">
        <strong style="font-weight:400;color:#555">Pellentesque habitant morbi</strong>
        <p style="margin-top:3px;text-align:justify">tristique senectus et netus fames ac turpis egestas. Vestibulum tortor quam, feugiat vitae,</p>
        <strong style="color:#666">Read More...</strong>
      </div>
      <svg class="abs" style="left:130px;top:66px" width="24" height="16" viewBox="0 0 24 16"><path d="M0 0 H24 L20 16 Z" fill="#fff"/></svg>
    </div>
    <span class="abs" style="left:628px;top:350px;font-size:9px;color:#888">Pellentesque</span>
    <div class="card abs" style="left:504px;top:370px;width:187px;height:26px;font-size:7px;color:#666;padding:8px 7px">Pellentesque habitant morbi tristique senectus</div>

    <section class="card abs" style="left:505px;top:408px;width:185px;height:172px">
      <div class="fb-head abs">Reader Comments
        <span class="abs" style="right:8px;top:3px;width:20px;height:20px;border-radius:50%;background:#6d82b3"></span>
      </div>
      <div class="abs" style="left:10px;top:36px;width:51px;height:15px;background:var(--blue);color:#fff;font-size:8px;font-weight:700;text-align:center;line-height:15px">Login</div>
      <p class="abs" style="left:74px;top:37px;width:100px;font-size:5.5px;line-height:7.5px;color:#888">You need to be logged into to see comments</p>
      <div class="abs" style="left:10px;top:61px;width:150px;border-top:1px solid #e3e3e3"></div>
      <div class="avatar abs" style="left:9px;top:69px" role="img" aria-label="Commenter avatar"></div>
      <p class="fb-text abs" style="left:47px;top:72px;width:130px">Lorem Ipsum is simply dummy text of the printing and typesetting industry.<small>6 People Viewed your Comments</small></p>
      <div class="avatar abs" style="left:9px;top:107px" role="img" aria-label="Commenter avatar"></div>
      <p class="fb-text abs" style="left:47px;top:110px;width:130px">Lorem Ipsum is simply dummy text of the printing and typesetting industry.<small>6 People Viewed your Comments</small></p>
      <div class="abs" style="left:10px;top:150px;width:165px;border-top:1px solid #e3e3e3"></div>
      <span class="abs" style="left:10px;top:157px;width:9px;height:9px;background:var(--blue)"></span>
      <span class="abs" style="left:27px;top:157px;font-size:6px;color:#444">Comments Plugin</span>
      <span class="abs" style="left:127px;top:156px;font-size:5.5px;color:#555;border:1px solid #c9c9c9;padding:1px 3px;background:#eef1f7">Like</span>
      <span class="abs" style="left:151px;top:156px;font-size:5.5px;color:#555;border:1px solid #c9c9c9;padding:1px 3px">203K</span>
    </section>
  </main>

  <footer class="footer abs">
    <div class="foot-links abs">Home<span>|</span>About<span>|</span>Work With Us<span>|</span>Testimonials<span>|</span>Giving Back<span>|</span>Contact Us<br>Copyright ©2012 - All rights reserved</div>
    <div class="socials abs"><i></i><i></i><i></i><i></i><i></i></div>
  </footer>

</div>
</body>
</html>
```